Stylish new business card needed!

Hello everyone! I am in need of a new business card design for an alarm company here in Hurricane WV. I have all fonts, color codes and logos provided for you use! We are a young company and like the style of a clean sleek looking business card. Would like it double sided, one side holding the logo and the other with your design!
Target Market(s)
The people that are looking for the newest tech for home automation and security
Industry/Entity Type
Alarm services; Home automation
Contact Information for Business Card
Name of person; position (Sales; Installer); Phone Number (555.418.7260); Employee cell Number; Website (www.GuardedByVelk.example); Employee Email; Double sided
Look and feel
Each slider illustrates characteristics of the customer's brand and the style your logo design should communicate.

```html
<!DOCTYPE html>
<html lang="en">
<head>
<meta charset="utf-8">
<title>Velk business card – front and back</title>
<link rel="stylesheet" href="https://fonts.googleapis.com/css2?family=Montserrat:wght@400;500;600&display=swap">
<style>
  :root {
    --backdrop: #c9c9c9;
    --card: #999999;
    --accent: #f28c4a;
    --ink: #ffffff;
  }
  * { margin: 0; padding: 0; box-sizing: border-box; }
  html, body {
    width: 1200px; height: 788px; overflow: hidden;
    background: var(--backdrop);
    font-family: "Montserrat", sans-serif;
  }
  .stage {
    position: relative; width: 1200px; height: 788px;
    display: flex; align-items: center; justify-content: center; gap: 60px;
  }
  .card {
    position: relative; width: 520px; height: 298px;
    background: var(--card); border-radius: 22px; overflow: hidden;
    color: var(--ink);
  }
  .company-name {
    font-family: "Montserrat", sans-serif;
    font-weight: 500; color: var(--ink); letter-spacing: 3px;
    line-height: 1;
  }

  /* front */
  .card-front .company-name { position: absolute; left: 40px; top: 84px; font-size: 44px; }
  .name-block { position: absolute; right: 46px; top: 29px; text-align: right; }
  .person-name { color: var(--accent); font-weight: 600; font-size: 18px; letter-spacing: 1.5px; line-height: 1.2; }
  .person-role { font-size: 12px; margin-top: 4px; letter-spacing: .5px; }
  .edge-tab { position: absolute; right: 0; top: 24px; width: 30px; height: 30px; background: var(--accent); }
  .address { position: absolute; left: 42px; top: 162px; font-size: 13px; line-height: 1.45; letter-spacing: .4px; }
  .contact-list { position: absolute; left: 42px; top: 214px; list-style: none; font-size: 13.5px; line-height: 1.55; letter-spacing: .4px; }
  .contact-list li { display: flex; align-items: center; gap: 8px; }
  .contact-list svg { width: 12px; height: 12px; flex: none; }

  /* back */
  .card-back { display: flex; align-items: center; justify-content: center; }
  .card-back .company-name { font-size: 84px; letter-spacing: 5px; }
</style>
</head>
<body>
<main class="stage">
  <section class="card card-front" aria-label="Card front">
    <div class="edge-tab"></div>
    <div class="name-block">
      <p class="person-name">DANA REYES</p>
      <p class="person-role">Sales/Installer</p>
    </div>
    <p class="company-name">VELK</p>
    <p class="address">418 Birch Hollow Road<br>Marlow County Line 4470</p>
    <ul class="contact-list">
      <li>
        <svg viewBox="0 0 12 12" aria-hidden="true"><path fill="#f28c4a" d="M2.4 0.8l1.8 2.4-1 1.1c.6 1.4 1.6 2.4 3 3l1.1-1 2.4 1.8-.9 2C5.3 10.5 1.5 6.7.4 2.4z"/></svg>
        <span>555.418.7260</span>
      </li>
      <li>
        <svg viewBox="0 0 12 12" aria-hidden="true"><rect x="0.5" y="2" width="11" height="8" fill="#f28c4a"/><path d="M0.8 2.4L6 6.6l5.2-4.2" stroke="#999" stroke-width="1" fill="none"/></svg>
        <span>info@GuardedByVelk.example</span>
      </li>
      <li>
        <svg viewBox="0 0 12 12" aria-hidden="true"><circle cx="6" cy="6" r="5.2" fill="none" stroke="#f28c4a" stroke-width="1.2"/><ellipse cx="6" cy="6" rx="2.2" ry="5.2" fill="none" stroke="#f28c4a" stroke-width="1"/><path d="M0.8 6h10.4" stroke="#f28c4a" stroke-width="1"/></svg>
        <span>www.GuardedByVelk.example</span>
      </li>
    </ul>
  </section>

  <section class="card card-back" aria-label="Card back">
    <p class="company-name">VELK</p>
  </section>
</main>
</body>
</html>
```